Fin-Tech Firm Captivating Business Card Design

We need a logo design as well to compliment this business card.

We are a new startup based in Singapore called 'Brevora Technologies'.

We develop an array of financial solutions ranging from payment convenience to forex trading and remittance.

Our initial product is Pim - an application which allows user to pre-order food items which would be ready for pickup upon arrival.

We would like to see designs being in black and silver or whatever that looks appealing and exudes a fun and professional feel.

We're not picky as long as it doesn't look like common business cards will do.

I do have a current logo which i do not really like. It will be attached for reference sake

Info:

Brevora Technologies Pte. Ltd.
Company Registration no. 201678213K

FILE TO BE IN .AI and .PSD

Target Market(s)

-F&B (Online-Ordering)
-Finance(P2P Lending and Forex)

Industry/Entity Type

Finance

Contact Information for Business Card

Name
Position
Contact
Email
Address: 47 Merrow Street, Calder House, #14-03 Singapore 068215

Adrian Teo
Founder, Managing Director
+65 98471360
adrian.t@brevoratech.com

Kai Loh
Founder, Executive Director
+65 96603847
kai.l@brevoratech.com

Logo Text

Brevora Technologies

Font styles to use
Sans Serif

Requirements
Must have
• Something that has word play about link brev
• Minimalistic but also something that catches The Eye
• Gold/silver on white/black might be nice
• Animal logo ; horse, eagle, bull or bear
Nice to have
• Just make it look fun and cute
• Just a suggestion to make the Y of brevora stand out
Should not have
• Any landmarks of singapore
• Exclude Pte. Ltd.

```html
<!DOCTYPE html>
<html lang="en">
<head>
<meta charset="utf-8">
<title>Brevora Technologies – Business Card</title>
<link href="https://fonts.googleapis.com/css2?family=Open+Sans:wght@400;600;700&display=swap" rel="stylesheet">
<style>
  :root {
    --page-bg: #e9e6e1;
    --gold: #c19708;
    --gold-text: #d9a514;
    --ink: #1d1d1d;
    --white: #ffffff;
    --silver: #a7a7a7;
    --card-shadow: 0 10px 30px rgba(0,0,0,0.18);
  }
  * { box-sizing: border-box; margin: 0; padding: 0; }
  html, body {
    width: 1200px; height: 900px; overflow: hidden;
    background: var(--page-bg);
    font-family: "Open Sans", sans-serif;
  }
  .sheet {
    width: 1200px; height: 900px;
    display: flex; flex-direction: column;
    align-items: center; justify-content: center; gap: 40px;
  }
  .card {
    width: 720px; height: 410px;
    position: relative;
    box-shadow: var(--card-shadow);
    overflow: hidden;
  }

  /* Back of card */
  .card-back { background: var(--gold); }
  .card-back .wordmark {
    position: absolute; left: 0; right: 0; bottom: 120px;
    text-align: center;
    color: var(--white);
    font-weight: 400;
    font-size: 40px;
    letter-spacing: 2px;
  }
  .card-back .tagline {
    position: absolute; left: 0; right: 0; bottom: 84px;
    display: flex; align-items: center; justify-content: center; gap: 14px;
    color: var(--white); font-size: 20px;
  }
  .rule { width: 60px; height: 1px; background: currentColor; }

  /* Front of card */
  .card-front { background: var(--white); }
  .contact {
    position: absolute; left: 340px; top: 44px;
    color: var(--ink);
  }
  .contact .person-name { color: var(--gold-text); font-weight: 700; font-size: 24px; line-height: 1.2; }
  .contact .person-role { font-size: 17px; margin-top: 2px; }
  .contact .address { font-size: 17px; line-height: 1.45; margin-top: 22px; }
  .contact .lines { margin-top: 22px; font-size: 17px; line-height: 1.6; }
  .contact .line { display: flex; align-items: center; gap: 10px; }
  .contact .line svg { width: 15px; height: 15px; fill: var(--gold-text); flex: none; }
  .contact .registration {
    margin-top: 26px; color: var(--gold-text); font-weight: 600; font-size: 17px;
  }
  .brand {
    position: absolute; left: 50px; bottom: 52px; width: 250px;
    display: flex; flex-direction: column; align-items: center;
  }
  .brand-dot {
    width: 112px; height: 112px; border-radius: 50%;
    background: var(--silver);
    margin-bottom: 16px;
  }
  .brand-name {
    color: var(--gold-text); font-weight: 400; font-size: 34px; letter-spacing: 1px; line-height: 1.2;
  }
  .brand-sub {
    display: flex; align-items: center; gap: 10px;
    color: var(--silver); font-size: 16px; margin-top: 2px;
  }
  .brand-sub .rule { width: 36px; }
</style>
</head>
<body>
<main class="sheet">
  <section class="card card-back" aria-label="Card back">
    <div class="wordmark">Brevora</div>
    <div class="tagline"><span class="rule"></span><span>Technologies</span><span class="rule"></span></div>
  </section>

  <section class="card card-front" aria-label="Card front">
    <div class="brand">
      <div class="brand-dot"></div>
      <div class="brand-name">Brevora</div>
      <div class="brand-sub"><span class="rule"></span><span>Technologies</span><span class="rule"></span></div>
    </div>

    <div class="contact">
      <div class="person-name">Adrian Teo</div>
      <div class="person-role">Founder, Managing Director</div>
      <div class="address">47 Merrow Street, Calder House,<br>#14-03 Singapore 068215</div>
      <div class="lines">
        <div class="line">
          <svg viewBox="0 0 24 24" aria-hidden="true"><path d="M6.6 10.8a15.1 15.1 0 0 0 6.6 6.6l2.2-2.2c.3-.3.7-.4 1-.2 1.1.4 2.3.6 3.6.6.6 0 1 .4 1 1V20c0 .6-.4 1-1 1A17 17 0 0 1 3 4c0-.6.4-1 1-1h3.5c.6 0 1 .4 1 1 0 1.3.2 2.5.6 3.6.1.3 0 .7-.2 1z"/></svg>
          <span>+65 98471360</span>
        </div>
        <div class="line">
          <svg viewBox="0 0 24 24" aria-hidden="true"><path d="M2 5h20v14H2z" fill="var(--gold-text)"/><path d="M3 6l9 6.3L21 6" stroke="#fff" stroke-width="1.6" fill="none"/></svg>
          <span>adrian.t@brevoratech.com</span>
        </div>
      </div>
      <div class="registration">Company Registration no. 201678213K</div>
    </div>
  </section>
</main>
</body>
</html>
```